Business Card Design for a Software Startup

We'd like to have a business card design. We already have a logo. Basically what we need is a clean design with name, address, cellphone and phone numbers, e-mail and web site address (front) and a space on the back with our logo with the company name on the right side and some texts on the bottom.
We are a development and consulting company in Brazil with highly qualified team of professionals in Java, iOS and Android development and consulting.

Target Market(s)

CIO, IT managers of mid to big size companies

Industry/Entity Type

Business

```html
<!DOCTYPE html>
<html lang="en">
<head>
<meta charset="utf-8">
<title>Vantyx Business Card</title>
<link rel="stylesheet" href="https://fonts.googleapis.com/css2?family=Open+Sans:wght@400;600;700&display=swap">
<style>
  :root {
    --bg: #e9e9ee;
    --card: #ffffff;
    --navy: #0b2d5b;
    --blue: #1b6cb3;
    --sky: #1ea8e4;
    --ink: #2a2a2a;
    --rule: #d6d6d6;
  }
  * { margin: 0; padding: 0; box-sizing: border-box; }
  html, body { width: 1200px; height: 987px; overflow: hidden; }
  body {
    background: var(--bg);
    font-family: "Open Sans", Arial, sans-serif;
    position: relative;
  }
  .card {
    position: absolute;
    left: 280px;
    width: 640px;
    height: 366px;
    background: var(--card);
    border-radius: 28px;
    overflow: hidden;
    box-shadow: 0 6px 18px rgba(0,0,0,0.12);
  }
  .card--front { top: 90px; }
  .card--back  { top: 531px; }

  .front-waves { position: absolute; left: 0; top: 0; width: 640px; height: 366px; }

  .brand {
    position: absolute;
    display: flex;
    align-items: center;
    gap: 14px;
    color: var(--navy);
    font-weight: 700;
    letter-spacing: 2px;
  }
  .brand__square {
    background: var(--blue);
    border-radius: 6px;
    flex: none;
  }
  .card--front .brand { left: 44px; top: 92px; font-size: 44px; }
  .card--front .brand__square { width: 46px; height: 46px; }

  .divider {
    position: absolute;
    left: 330px; top: 40px;
    width: 1px; height: 190px;
    background: var(--rule);
  }

  .contact { position: absolute; left: 352px; top: 44px; color: var(--ink); }
  .contact__name { color: var(--blue); font-weight: 700; font-size: 24px; line-height: 1.1; }
  .contact__title { font-size: 17px; margin-bottom: 14px; }
  .contact__list { list-style: none; font-size: 17px; line-height: 1.45; }
  .contact__list li { display: flex; align-items: center; gap: 8px; }
  .contact__list svg { width: 14px; height: 14px; flex: none; fill: var(--navy); }
  .contact__address { font-size: 17px; line-height: 1.4; margin-top: 14px; }

  .card--back .brand {
    left: 0; right: 0; top: 118px;
    justify-content: center;
    font-size: 70px;
  }
  .card--back .brand__square { width: 66px; height: 66px; }
  .back-url {
    position: absolute;
    left: 0; right: 0; top: 240px;
    text-align: center;
    color: #444;
    font-size: 20px;
    letter-spacing: 5px;
  }
</style>
</head>
<body>
  <section class="card card--front">
    <svg class="front-waves" viewBox="0 0 640 366" aria-hidden="true">
      <defs>
        <linearGradient id="wave-fill" x1="0" y1="0" x2="1" y2="1">
          <stop offset="0" stop-color="#1ea8e4"/>
          <stop offset="1" stop-color="#2a3f7e"/>
        </linearGradient>
      </defs>
      <path d="M0 190 C120 180 260 240 360 366 L0 366 Z" fill="url(#wave-fill)"/>
      <path d="M0 176 C140 168 300 240 420 366 L402 366 C290 250 140 188 0 196 Z" fill="#0b2d5b"/>
      <path d="M0 168 C150 150 330 230 460 366 L450 366 C320 236 150 160 0 176 Z" fill="#ffffff"/>
    </svg>

    <div class="brand"><span class="brand__square"></span>VANTYX</div>

    <div class="divider"></div>

    <div class="contact">
      <p class="contact__name">Your Name</p>
      <p class="contact__title">Title</p>
      <ul class="contact__list">
        <li><svg viewBox="0 0 16 16"><path d="M3 1l3 3-2 2c1 2 3 4 5 5l2-2 3 3-2 3C7 15 1 9 0 4z"/></svg>123-456-7890</li>
        <li><svg viewBox="0 0 16 16"><rect x="4" y="0" width="8" height="16" rx="2"/></svg>456-085-4321</li>
        <li><svg viewBox="0 0 16 16"><path d="M0 3h16v10H0z M0 3l8 6 8-6" stroke="#fff" stroke-width="1"/></svg>yourname@vantyx.com</li>
        <li><svg viewBox="0 0 16 16"><circle cx="8" cy="8" r="7"/></svg>www.vantyx.com</li>
      </ul>
      <p class="contact__address">Door No. Street Name<br>City Name, State, Zip Code</p>
    </div>
  </section>

  <section class="card card--back">
    <div class="brand"><span class="brand__square"></span>VANTYX</div>
    <p class="back-url">www.vantyx.com</p>
  </section>
</body>
</html>
```